Environmental Consultancey needs Web Design

A consultancey firm based in Papua New Guinea specialising servicing a client market primarily in Melanesia, the wider Pacific Region and South East Asia. The firm provides services to community development and resource extraction activites that incorporate sustainable livelihoods for local customary land owners with environmentally responsibile practices and a focus on maintaining biodiversity and ecosystem services. We aim to encompass Culture, Custom and Science in our approach. Our website preferentially will convey a relaxed Pacific Island feel in its colours and design rather than a sterile corporate feel. See attached logo that will need to be visible on page or which may provide basis for ideas for the page.

Target Market(s)

Our target market is primarily the oil, gas and mining industry, secondarily international donor and aid programs followed by government projects and not for profit programs. Services include:
1. Biodiversity and Conservation - Fauna and Flora survey, assessment, management, monitoring & research, protected areas & endangered & threatend species.
2. Social & Community - impact, stakeholder engagement, census and survey, land and community affairs, capacity building empowerment.
3. Environmental Management - sustainable use, enterprise development & management, biodiversity offsets.

Industry/Entity Type

Community

Requirements
Must have
• Multiple pages, Logo somewhere on home page. Space for a couple of photos that as yet ive not decieded upon.
Nice to have
• Perhaps incorporate shapes, texture and colours that convey a feel of the attached photo of a blue bird of paradise. The blue fine overlapping and interlocking feather patterns are appealing perhaps as a background and the other colours used in boarders ? Abstract is fine as would be symbolic images or tribal ambience. The company is all about blending humanity in all its forms with the environment.

```html
<!DOCTYPE html>
<html lang="en">
<head>
<meta charset="utf-8">
<title>Kundu Environmental</title>
<link rel="stylesheet" href="https://fonts.googleapis.com/css2?family=Cabin:wght@400;500;600&display=swap">
<style>
:root{
  --sky-top:#0b5b8e;
  --sky-bottom:#c6e3f1;
  --panel:#ffffff;
  --ink:#333333;
  --ink-soft:#444444;
  --heading:#1f3f5c;
  --accent:#1a6f95;
  --nav-red:#d81e22;
  --nav-blue-a:#e8f5fc;
  --nav-blue-b:#a9d7ee;
  --leaf-a:#8fd33a;
  --leaf-b:#f4fbe9;
  --frame:#d9d9d9;
  --button-green:#3c8f13;
}
*{box-sizing:border-box;margin:0;padding:0}
html,body{width:898px;height:1200px;overflow:hidden}
body{
  position:relative;
  background:linear-gradient(180deg,var(--sky-top) 0%,#3a86b8 35%,#8cc3e0 70%,var(--sky-bottom) 100%);
  font-family:Arial,Helvetica,sans-serif;color:var(--ink);
}
.abs{position:absolute}
/* header */
.site-header{left:31px;top:31px;width:838px;height:204px;background:var(--panel);border-radius:6px;overflow:hidden}
.brand{left:28px;top:60px;display:flex;align-items:center;gap:10px}
.brand-dot{width:34px;height:34px;border-radius:50%;background:#1b7fb3}
.brand-name{font-family:'Cabin',sans-serif;font-weight:600;font-size:20px;color:#1b4e73;line-height:1.15;width:140px}
.header-photo{left:498px;top:0;width:340px;height:170px;
  background:linear-gradient(90deg,#ffffff 0%,#cfe6ef 12%,#6fb0d6 40%,#2d79bf 65%,#9fcbe0 100%)}
.search{left:573px;top:45px;width:246px;height:62px;background:rgba(255,255,255,.55);border-radius:4px}
.search-label{left:28px;top:10px;font-size:13px;color:#222}
.search-field{left:25px;top:30px;width:140px;height:22px;border:1px solid #888;border-radius:4px;background:linear-gradient(#e8e8e8,#fff)}
.search-go{left:178px;top:30px;width:34px;height:22px;border-radius:4px;background:linear-gradient(#fff35a,#f3c400);font-size:11px;text-align:center;line-height:22px;color:#222}
.nav{left:0;top:172px;width:838px;height:32px;background:linear-gradient(var(--nav-blue-a),var(--nav-blue-b));display:flex;align-items:center;padding-left:18px}
.nav a{font-family:'Cabin',sans-serif;font-weight:600;font-size:13px;letter-spacing:.3px;color:#1c2a36;text-decoration:none;padding:5px 16px;border-radius:3px}
.nav a.current{background:linear-gradient(#ee3a3a,var(--nav-red));color:#fff;margin-right:4px}
/* main */
.main{left:31px;top:243px;width:838px;height:830px;background:var(--panel);border-radius:6px}
.slider{left:24px;top:19px;width:798px;height:259px;background:var(--frame);border-radius:6px}
.slide{left:11px;top:13px;width:776px;height:233px;
  background:linear-gradient(180deg,#8fc4ea 0%,#cde6f7 55%,#b8d99a 78%,#4f8f1f 100%)}
.slide-caption{left:0;top:92px;width:385px;height:60px;background:rgba(255,255,255,.6);font-family:'Cabin',sans-serif;font-size:21px;color:#1d3d5a;line-height:60px;padding-left:10px}
.slider-tab{left:347px;top:263px;width:152px;height:24px;background:linear-gradient(#fff,#e1e1e1);border-radius:0 0 4px 4px;display:flex;justify-content:center;align-items:center;gap:7px}
.slider-tab span{width:9px;height:9px;border-radius:50%;background:#c9c9c9;border:1px solid #aaa}
.slider-tab span.on{background:#777}
.widget{width:226px;background:#fff;border:2px solid #dcdcdc;border-radius:14px;overflow:hidden}
.widget-head{height:44px;background:linear-gradient(180deg,var(--leaf-a),var(--leaf-b));font-family:'Cabin',sans-serif;font-size:16px;color:#1c3550;display:flex;align-items:center;padding-top:6px}
.login{left:28px;top:317px;height:144px}
.login .widget-head{padding-left:12px;gap:8px}
.icon-box{width:22px;height:26px;border-radius:4px;background:#9a4d18}
.field-row{display:flex;align-items:center;margin:8px 0 0 14px;font-family:Georgia,serif;font-size:12px;color:#444}
.field-row label{width:74px;text-align:right;padding-right:8px}
.field-row span{width:112px;height:21px;border:1px solid #999;background:#f7f7f7}
.submit{margin:8px 0 0 88px;width:66px;height:24px;border-radius:4px;background:linear-gradient(#6ecb2a,var(--button-green));color:#fff;font-size:12px;text-align:center;line-height:24px}
.tweets{left:28px;top:485px;height:166px}
.tweets .widget-head{height:48px;padding-left:8px;gap:12px}
.news-dot{width:36px;height:36px;border-radius:50%;background:#2fa2d8}
.tweets .widget-head .title{margin-left:40px}
.tweet-body{padding:22px 8px 0 8px;font-size:10.5px;line-height:13px;color:#222}
.tweet-body p+p{margin-top:10px}
.welcome{left:291px;top:331px;width:520px}
.welcome h1{font-family:'Cabin',sans-serif;font-weight:400;font-size:16px;color:var(--heading);margin-bottom:16px}
.welcome h1 em{font-style:normal;color:var(--accent)}
.welcome p{font-size:11px;line-height:15.5px;color:var(--ink-soft);margin-bottom:16px;white-space:nowrap}
.read-more{left:743px;top:624px;font-family:'Cabin',sans-serif;font-size:11px;color:var(--accent)}
.projects-title{left:39px;top:665px;font-family:'Cabin',sans-serif;font-weight:400;font-size:16px;color:var(--heading)}
.projects{left:28px;top:690px;width:803px;height:130px;border:2px solid #d9d9d9;border-radius:6px;background:linear-gradient(#fff,#f5f5f5)}
.arrow{top:50px;width:24px;height:24px;border-radius:50%;background:#1f1f1f}
.arrow svg{display:block}
.thumb{top:21px;width:116px;height:82px}
/* footer */
.footer{left:31px;top:1087px;width:838px;height:94px;border-radius:4px;
  background:linear-gradient(90deg,#b6e27a 0%,#ffffff 25%,#ffffff 45%,#e7f7d0 70%,#a6dc4e 100%)}
.social{left:36px;top:27px;display:flex;gap:5px}
.social span{width:37px;height:37px;border-radius:50%;background:#2a4f92;border:2px solid #cfd8e4}
.footer-links{left:464px;top:27px;font-size:11px;color:#222}
.footer-links b{font-weight:400;margin:0 14px}
.copyright{left:449px;top:58px;font-size:11px;color:#222}
</style>
</head>
<body>
<header class="site-header abs">
  <div class="brand abs"><span class="brand-dot"></span><span class="brand-name">Kundu Environmental</span></div>
  <div class="header-photo abs" role="img" aria-label="Close-up of a blue bird of paradise on a branch"></div>
  <div class="search abs">
    <span class="search-label abs">SEARCH</span>
    <span class="search-field abs"></span>
    <span class="search-go abs">Go</span>
  </div>
  <nav class="nav abs">
    <a class="current" href="#">Home</a><a href="#">About Us</a><a href="#">Support</a><a href="#">Services</a><a href="#">Contact Us</a>
  </nav>
</header>

<main class="main abs">
  <div class="slider abs">
    <div class="slide abs" role="img" aria-label="Young green seedling growing from grass under a blue sky">
      <div class="slide-caption abs">Encompassing Culture, Custom &amp; Science</div>
    </div>
  </div>
  <div class="slider-tab abs"><span class="on"></span><span></span><span></span><span></span><span></span></div>

  <section class="widget login abs">
    <div class="widget-head"><span class="icon-box" role="img" aria-label="User icon"></span>Login</div>
    <div class="field-row"><label>User Name :</label><span></span></div>
    <div class="field-row"><label>Password :</label><span></span></div>
    <div class="submit">Submit</div>
  </section>

  <section class="widget tweets abs">
    <div class="widget-head"><span class="news-dot"></span><span class="title">Latest Updates</span></div>
    <div class="tweet-body">
      <p>We just launched a new site! Check it out and stay tuned for a few others to be launched this month!! http://kunduenv.pg/n4<br>1 week ago</p>
      <p>Follow our news &gt;&gt;</p>
    </div>
  </section>

  <section class="welcome abs">
    <h1>Welcome to <em>Kundu Environmental</em></h1>
    <p>You can take advantage of theHome Efficiency program right now – but since it'soffered on a<br>first-come, first-served basis, interested customers quickly to take advantage of availableincentives.<br>The program is in effect untilfunding is no longer available or it is discontinued by the Commission.</p>
    <p>&nbsp;Is your home leaking money without you even knowing it?</p>
    <p>&nbsp;Are you a home owner desiring to lower your monthly utility bills and begin saving money?</p>
    <p>&nbsp;Ready for additional rebates and incentives of up to $6,000 (varies by city and county)?</p>
    <p>&nbsp;Want to takeadvantage of a limited opportunity to receive 100% financing and 3%fixed interest<br>rates, with no credit or equity required?</p>
    <p>&nbsp;What if the payment on the low interest loan was less than the projected savings on your<br>monthly utility bills?</p>
  </section>
  <span class="read-more abs">&gt;&gt;&nbsp;&nbsp;Read More</span>

  <h2 class="projects-title abs">Our Projects</h2>
  <section class="projects abs">
    <span class="arrow abs" style="left:8px"><svg width="24" height="24"><path d="M14 8l-4 4 4 4" fill="none" stroke="#fff" stroke-width="2"/></svg></span>
    <div class="thumb abs" style="left:52px;width:92px;background:linear-gradient(135deg,#4a8fd0,#7fc04a)" role="img" aria-label="Recycling arrows around a globe"></div>
    <div class="thumb abs" style="left:171px;background:linear-gradient(180deg,#dfe9ef,#2c8fb2 50%,#e6eef2)" role="img" aria-label="Blue lagoon surrounded by ice"></div>
    <div class="thumb abs" style="left:320px;background:linear-gradient(135deg,#5a4a2e,#2f6e9c 50%,#3d3322)" role="img" aria-label="Hands holding a globe among photo collage"></div>
    <div class="thumb abs" style="left:469px;background:linear-gradient(180deg,#2a211a,#5b4330 60%,#3a2a1d)" role="img" aria-label="Hands holding soil with a green sprout"></div>
    <div class="thumb abs" style="left:618px;background:linear-gradient(180deg,#1c1c1c,#b97f5a 45%,#2f5f9a 70%,#111)" role="img" aria-label="Hands cupped around planet Earth"></div>
    <span class="arrow abs" style="left:763px"><svg width="24" height="24"><path d="M10 8l4 4-4 4" fill="none" stroke="#fff" stroke-width="2"/></svg></span>
  </section>
</main>

<footer class="footer abs">
  <div class="social abs"><span></span><span></span><span></span></div>
  <div class="footer-links abs">Terms &amp; Conditions<b>|</b>Privacy<b>|</b>Contact us</div>
  <div class="copyright abs">Copyright © 2012 KunduEnvironmental, All Rights Reserved</div>
</footer>
</body>
</html>
```